Quorbelline.io - Please redesign to make it look better from current design

We already have the current website, that you can access but we think it can improve from current version.
Quorbelline is a cryptocurrency hedge fund that allow you to participate in the hedge fund with cryptocurrency such as eth.
At current phase, we are doing an ICO, then we want to make sure that the website it looks professional, beautiful and trustable enough for investors after looking at our website.
Target Market(s)
Investors
Industry/Entity Type
Investment
Coding
Coded - Design and coding required
Number of Pages Required
1 page
Look and feel
Each slider illustrates characteristics of the customer's brand and the style your logo design should communicate.

```html
<!DOCTYPE html>
<html lang="en">
<head>
<meta charset="utf-8">
<title>Quorbelline.io – Digital Asset Management</title>
<link rel="stylesheet" href="https://fonts.googleapis.com/css2?family=Raleway:wght@400;500;600;700;800&family=Lato:ital,wght@0,400;0,700;1,700&display=swap">
<style>
:root{
  --navy:#1b2a86;
  --navy-dark:#14206a;
  --ink:#222;
  --grey-text:#6b6b6b;
  --light-panel:#eeeeee;
  --charcoal:#333333;
  --white:#ffffff;
  --bubble:#d6f0fb;
  --bubble-ring:#9fd6ee;
  --footer-grey:#a9a9a9;
}
*{margin:0;padding:0;box-sizing:border-box}
html,body{width:1200px;height:3364px;overflow:hidden;background:var(--white)}
body{position:relative;font-family:'Lato',sans-serif;color:var(--ink)}
.abs{position:absolute}
.heading{font-family:'Raleway',sans-serif}

/* hero */
.hero{left:0;top:0;width:1200px;height:628px;background:linear-gradient(135deg,#e9ecef 0%,#d6dbe0 45%,#f2f3f4 100%)}
.brand{left:0;width:1200px;top:150px;text-align:center;font-family:'Raleway',sans-serif;font-weight:700;font-size:50px;color:var(--navy);letter-spacing:1px}
.brand-dot{display:inline-block;width:26px;height:26px;border-radius:50%;background:var(--navy);margin-right:16px;vertical-align:middle}
.hero-title{left:0;width:1200px;top:340px;text-align:center;font-weight:700;font-size:31px;color:var(--navy)}
.hero-text{left:360px;width:480px;top:396px;text-align:center;font-size:15px;line-height:22px;color:#555}
.btn{display:flex;align-items:center;justify-content:center;background:var(--navy-dark);color:var(--white);font-family:'Raleway',sans-serif;font-size:21px;letter-spacing:1px;border-radius:8px;box-shadow:0 3px 6px rgba(0,0,0,.3)}
.hero-btn{left:497px;top:485px;width:206px;height:50px}

/* definition */
.definition{left:0;top:628px;width:1200px;height:669px;background:var(--navy);border-bottom-left-radius:70px}
.definition-panel{left:370px;top:635px;width:830px;height:655px;background:var(--light-panel);border-top-left-radius:45px;border-bottom-left-radius:45px}
.section-label{font-family:'Raleway',sans-serif;font-weight:600;color:var(--white);font-size:52px}
.def-label{left:63px;top:900px}
.def-text{left:449px;width:673px;top:692px;text-align:center;font-size:14px;line-height:24px;color:#555}
.read-more{font-family:'Lato',sans-serif;font-style:italic;font-weight:700;font-size:17px;color:var(--navy);text-decoration:underline}
.def-more{left:1020px;top:822px}
.def-band{left:700px;top:902px;width:500px;height:282px}
.monitor{left:756px;top:881px;width:293px;height:308px;border-radius:10px;background:linear-gradient(180deg,#4b4f57 0%,#2f3238 70%,#c9ccd0 72%,#e4e6e8 100%)}
.more-info{left:406px;top:1020px;font-family:'Raleway',sans-serif;font-size:29px;line-height:34px;color:#222}
.whitepaper-btn{left:406px;top:1126px;width:323px;height:58px;font-size:21px}

/* team */
.team-back{left:0;top:1297px;width:1200px;height:800px;background:var(--charcoal);border-top-left-radius:70px;border-bottom-right-radius:70px}
.team-card{left:0;top:1297px;width:819px;height:800px;background:var(--white);border-top-right-radius:45px;border-bottom-right-radius:45px}
.team-label{left:864px;top:1650px;font-weight:700;font-size:50px}
.member{width:360px;text-align:center}
.avatar{width:188px;height:188px;border-radius:50%;margin:0 auto;border:2px solid var(--navy);background:radial-gradient(circle at 50% 40%,#c9c2bb 0%,#8d8a88 55%,#5a5b5e 100%)}
.member-name{font-family:'Raleway',sans-serif;font-weight:700;font-size:24px;margin-top:18px;color:#111}
.member-role{font-size:14px;color:#555;margin-top:4px}
.member-bio{font-size:14px;color:#555;line-height:20px;margin-top:4px}
.m1{left:62px;top:1377px}
.m2{left:419px;top:1377px}
.m3{left:257px;top:1714px}

/* process */
.process{left:0;top:2097px;width:1200px;height:663px;background:var(--navy);border-top-left-radius:70px}
.process-panel{left:381px;top:2101px;width:819px;height:655px;background:var(--white);border-top-left-radius:45px;border-bottom-left-radius:45px}
.process-label{left:85px;top:2402px}
.model-title{left:381px;width:794px;top:2150px;text-align:center;font-family:'Raleway',sans-serif;font-weight:700;font-size:26px;color:var(--navy)}
.model-text{left:445px;width:670px;top:2194px;text-align:center;font-size:14px;line-height:24px;color:#555}
.model-more{left:733px;top:2295px}
.npd-title{left:424px;top:2458px;font-family:'Raleway',sans-serif;font-weight:700;font-size:31px;color:var(--navy)}
.npd-line{left:424px;top:2512px;font-size:15px;color:var(--navy)}
.npd-rest{left:424px;top:2542px;width:370px;font-size:15px;line-height:22px;color:var(--navy);font-weight:700}
.npd-rest .big{font-family:'Raleway',sans-serif;font-size:33px;text-decoration:underline}
.tiers{left:780px;top:2300px;width:420px;height:520px;overflow:visible}
.tier-text{font-family:'Lato',sans-serif;fill:var(--navy-dark);text-anchor:middle}
.connector{left:540px;top:2756px;width:140px;height:110px}
.end-badge{left:543px;top:2853px;width:134px;height:134px;border-radius:50%;background:radial-gradient(circle,#111 0%,#111 52%,#555 54%,#222 62%,#bbb 64%,#888 72%,#ddd 74%,#eee 100%);display:flex;align-items:center;justify-content:center;color:var(--white);font-family:'Lato',sans-serif;font-weight:700;font-size:12px}

/* contact */
.plane{left:582px;top:3044px;width:36px;height:36px}
.contact-title{left:0;width:1200px;top:3090px;text-align:center;font-family:'Raleway',sans-serif;font-weight:800;font-size:50px;color:#111}
.location{left:0;width:1200px;top:3158px;text-align:center;font-family:'Raleway',sans-serif;font-size:22px;color:var(--navy);font-weight:500}
.location svg{vertical-align:-4px;margin-right:8px}
.address{left:0;width:1200px;top:3204px;text-align:center;font-size:15px;line-height:23px;color:var(--footer-grey)}
.rule{left:75px;top:3304px;width:1050px;height:1px;background:#c9cde0}
.footer{left:0;width:1200px;top:3324px;text-align:center;font-size:14px;color:#555}
.footer b{color:var(--navy);font-size:17px}
</style>
</head>
<body>

<!-- hero -->
<section class="abs hero" role="img" aria-label="Photo of hands holding a tablet showing financial charts"></section>
<div class="abs brand"><span class="brand-dot"></span>Quorbelline</div>
<h1 class="abs heading hero-title">Digital Asset Management</h1>
<p class="abs hero-text">Quorbelline enable companies and investors to facilities business operation in modern digital world, including asset management on hedge fund strategy model.</p>
<a class="abs btn hero-btn">READ MORE</a>

<!-- definition -->
<section class="abs definition"></section>
<div class="abs definition-panel"></div>
<h2 class="abs section-label def-label">Definition</h2>
<p class="abs def-text">Quorbelline process and manages on hedge fund strategy models which invests in a diversified portfolio of blockchain tokens. Blockchain tokens are emerging which add a monetary incentive layer to p2p protocols and facilitate equity crowdfunding that anyone in the world can participate in. This means open source software developers can monetize their networks at the protocol level and users of the network are the equity owners of the network. For this conditions, returns will go to holders of the tokens.</p>
<a class="abs read-more def-more">READ MORE</a>
<svg class="abs def-band" viewBox="0 0 500 282"><path d="M40 0 H500 V282 H60 A20 20 0 0 1 42 252 L110 90 L22 30 A18 18 0 0 1 40 0 Z" fill="var(--navy)"/></svg>
<div class="abs monitor" role="img" aria-label="Illustration of a desktop monitor displaying a rising blue bar chart"></div>
<p class="abs more-info">For More<br>INFORMATION</p>
<a class="abs btn whitepaper-btn">DOWNLOAD WHITEPAPER</a>

<!-- team -->
<section class="abs team-back"></section>
<div class="abs team-card"></div>
<h2 class="abs section-label team-label">OUR TEAM</h2>
<div class="abs member m1">
  <div class="avatar" role="img" aria-label="Portrait photo of Dariel Venhaskor"></div>
  <div class="member-name">Dariel Venhaskor</div>
  <div class="member-role">Director</div>
  <div class="member-bio">As a hedge fund manager. Venhaskor is the Chief Executive Officer of Brookhollow Capital LLC.</div>
</div>
<div class="abs member m2">
  <div class="avatar" role="img" aria-label="Portrait photo of Tavish Orlend"></div>
  <div class="member-name">Tavish Orlend</div>
  <div class="member-role">Technical advisor</div>
  <div class="member-bio">Orlend has various experienced on cryptocurrency and blockchain technology.</div>
</div>
<div class="abs member m3">
  <div class="avatar" role="img" aria-label="Portrait photo of Dariel Venhaskor"></div>
  <div class="member-name">Dariel Venhaskor</div>
  <div class="member-role">Director</div>
  <div class="member-bio">As a hedge fund manager. Venhaskor is the Chief Executive Officer of Brookhollow Capital LLC.</div>
</div>

<!-- process -->
<section class="abs process"></section>
<div class="abs process-panel"></div>
<h2 class="abs section-label process-label">Process</h2>
<h3 class="abs model-title">Hedge Fund Model</h3>
<p class="abs model-text">Quorbelline run on closed-end fund (CEF) model which offers its shares to investors and utilize the fund to speculate and invest in the innovative blockchain tokens. Quorbelline will charge an upfront annual operation fee 4% of the money raised during the ICO. After that, the fund will charge a quarterly performance of 50% on the net profit made.</p>
<a class="abs read-more model-more">READ MORE</a>
<h3 class="abs npd-title">Net Profit Distribution</h3>
<p class="abs npd-line">50 % of net profit is distributed to investors</p>
<p class="abs npd-rest"><span class="big">The remainder</span> : (50% minus performance fee, so at least 35%) is reinvested</p>

<svg class="abs tiers" viewBox="0 0 420 520">
  <path d="M45 84 H420 V459 H50 A30 30 0 0 1 20 429 V110 A26 26 0 0 1 45 84 Z" fill="var(--navy)"/>
  <g fill="var(--white)" stroke="var(--bubble-ring)" stroke-width="7">
    <circle cx="285" cy="107" r="85"/>
    <circle cx="173" cy="219" r="66"/>
    <circle cx="83" cy="342" r="50"/>
    <circle cx="184" cy="425" r="60"/>
  </g>
  <circle cx="300" cy="324" r="98" fill="var(--bubble)" stroke="var(--bubble-ring)" stroke-width="5"/>
  <g class="tier-text">
    <text x="285" y="97" font-size="15" font-weight="700">15 % netprofit</text>
    <text x="285" y="115" font-size="15">&gt;</text>
    <text x="285" y="133" font-size="15" font-weight="700">15 % performance fee</text>
    <text x="173" y="204" font-size="13" font-weight="700">10-15 % netprofit</text>
    <text x="173" y="220" font-size="13">&gt;</text>
    <text x="173" y="236" font-size="13" font-weight="700">13 % performance</text>
    <text x="173" y="251" font-size="13" font-weight="700">fee</text>
    <text x="83" y="324" font-size="11" font-weight="700">5-10 % netprofit</text>
    <text x="83" y="338" font-size="11">&gt;</text>
    <text x="83" y="352" font-size="11" font-weight="700">5 % performance</text>
    <text x="83" y="365" font-size="11" font-weight="700">fee</text>
    <text x="184" y="408" font-size="12" font-weight="700">0 - 5 % net profit</text>
    <text x="184" y="422" font-size="12">&gt;</text>
    <text x="184" y="437" font-size="12" font-weight="700">0 % performance</text>
    <text x="184" y="451" font-size="12" font-weight="700">fee</text>
    <text x="300" y="332" font-size="24" font-weight="700" font-family="Raleway, sans-serif">Quorbelline</text>
  </g>
</svg>

<svg class="abs connector" viewBox="0 0 140 110"><path d="M0 2 H30 Q70 2 70 40 V110" fill="none" stroke="var(--navy-dark)" stroke-width="6"/></svg>
<div class="abs end-badge">Quorbelline</div>

<!-- contact -->
<svg class="abs plane" viewBox="0 0 24 24"><path d="M2 11 L22 2 L15 22 L11 14 Z M11 14 L22 2" fill="var(--navy)" stroke="var(--navy)" stroke-width="1.2" stroke-linejoin="round"/></svg>
<h2 class="abs contact-title">CONTACT US</h2>
<div class="abs location"><svg width="18" height="24" viewBox="0 0 18 24"><path d="M9 1a8 8 0 0 0-8 8c0 6 8 14 8 14s8-8 8-14a8 8 0 0 0-8-8zm0 11a3 3 0 1 1 0-6 3 3 0 0 1 0 6z" fill="var(--footer-grey)"/></svg>Location</div>
<p class="abs address">Suites 04-12, 9/F, East Wing,<br>Meridian Trade Centre, Lantern Quay, 42 Lantern Road,<br>Harbourview, Kowloon, Hong Kong.</p>
<div class="abs rule"></div>
<p class="abs footer">© <b>Quorbelline</b> ·2017 All rights reserved.</p>

</body>
</html>
```